Online interactive calendar for training organisation

We have a new website being made and need a design for an online calendar that is interactive and very simple and easy to use. On our main page this calendar will include all of our courses (approx 30 different ones with up to 8 different locations). On our sub pages which have course information, the calendar will only include details of that specific course. Details needed are: Course code, course name/title, date, duration (1/2 day - 5 days), location, price, discount price. Maybe also a key for available or limited spots left? We want a section at the top of the calendar to be able to filter by location or course, and maybe to filter by month also? I have included a spreadsheet with a sample of our courses with this information. Also a sample draft of the main page on our new webpage to show the colour green which is our company colour. Main notes - we want as simple, effective and easy to use as possible.
We will need to know what plug in we can use to get the design you have created.

Target Market(s)

Mining and construction - both companies and individuals

Number of Pages Required

1 page

Colors
cadf82

Requirements
Must have
• Be simple, easy to use, effective.

```html
<!DOCTYPE html>
<html lang="en">
<head>
<meta charset="utf-8">
<title>Ridgeline Safety – Time Table</title>
<link href="https://fonts.googleapis.com/css2?family=Fira+Sans:wght@400;500;600;700&display=swap" rel="stylesheet">
<style>
:root{
  --green:#8dc63f;
  --green-soft:#cadf82;
  --brand-red:#d4261d;
  --ink:#222;
  --muted:#555;
  --line:#cfcfcf;
  --panel:#efefef;
  --dark:#2d2d2d;
  --tag-dark:#2f2f2f;
  --white:#fff;
}
*{box-sizing:border-box;margin:0;padding:0}
html,body{width:716px;height:1200px;overflow:hidden;background:var(--white)}
body{font-family:"Fira Sans",sans-serif;color:var(--ink)}
.page{position:relative;width:716px;height:1200px;overflow:hidden}
.abs{position:absolute}

/* top bar */
.topbar{left:0;top:0;width:716px;height:18px;background:var(--green)}
.social{display:flex;gap:3px}
.social span{width:11px;height:11px;border-radius:50%;background:var(--tag-dark);display:block}
.topbar .social{position:absolute;left:135px;top:4px}
.student-btn{position:absolute;left:465px;top:3px;width:50px;height:12px;background:var(--tag-dark);color:var(--white);font-size:5.5px;font-weight:600;display:flex;align-items:center;justify-content:center;border-radius:1px}
.search{position:absolute;left:519px;top:3px;width:63px;height:12px;background:var(--white);border-radius:1px}
.search svg{position:absolute;right:5px;top:3px}

/* header */
.header{left:0;top:18px;width:716px;height:42px;background:var(--white)}
.brand{position:absolute;display:flex;align-items:center;gap:5px}
.brand-mark{width:22px;height:22px;border-radius:50%;border:2px solid var(--brand-red)}
.brand-name{font-size:12px;font-weight:700;color:var(--brand-red);letter-spacing:.5px;line-height:1}
.brand-sub{font-size:5px;color:var(--ink);letter-spacing:.5px;margin-top:2px}
.header .brand{left:135px;top:8px}
.nav{position:absolute;display:flex;gap:10px;font-size:5.4px;color:var(--ink)}
.nav .active{color:var(--green)}
.header .nav{left:369px;top:18px}

/* categories */
.difference{left:0;top:60px;width:716px;height:320px;background:var(--panel)}
.section-title{position:absolute;left:0;width:716px;text-align:center;color:var(--ink)}
.difference h1{top:27px;font-size:17.5px;font-weight:400;letter-spacing:.2px}
.difference p{top:50px;font-size:6.8px;color:var(--ink)}
.difference .rule{position:absolute;left:344px;top:67px;width:29px;height:2px;background:var(--green-soft)}
.tile{position:absolute;width:82px}
.tile-img{width:82px;height:80px;border-radius:2px}
.tile-label{text-align:center;font-size:7px;color:var(--ink);margin-top:9px}
.img-dirt{background:linear-gradient(135deg,#6d6b65,#9a948a)}
.img-sky{background:linear-gradient(135deg,#3e9fe0,#8ecbf0)}
.img-quarry{background:linear-gradient(135deg,#8a8a84,#b23a2e)}
.img-site{background:linear-gradient(135deg,#7c7a70,#b9a45a)}
.img-roof{background:linear-gradient(135deg,#4c5a66,#a8b4bc)}
.img-office{background:linear-gradient(135deg,#3b3a3c,#b8b2ab)}
.img-team{background:linear-gradient(135deg,#6e8fa8,#e6b63b)}
.img-hardhat{background:linear-gradient(135deg,#5aa0d8,#e7e45a)}
.img-lift{background:linear-gradient(135deg,#6f8a6a,#e3c53c)}
.img-build{background:linear-gradient(135deg,#b77c3a,#d99a4e)}

/* timetable */
.timetable-title{top:414px;font-size:16px;font-weight:700;letter-spacing:.3px}
.timetable-rule{left:346px;top:439px;width:30px;height:3px;background:#bdbdbd}
.filter{position:absolute;top:471px;width:125px;height:26px;border:1.5px solid #c9c9c9;background:var(--white);padding:4px 7px}
.filter.active{border-color:var(--green)}
.filter-label{font-size:5.8px;font-weight:600;color:var(--ink);letter-spacing:.2px}
.filter-label b{color:var(--brand-red)}
.filter-value{font-size:7px;color:#666;letter-spacing:.3px;margin-top:1px}
.filter.active .filter-value{color:var(--green);font-weight:500}
.filter svg{position:absolute;right:9px;top:10px}

.course-card{position:absolute;width:171px;height:131px;border:1px solid #c4c4c4;background:var(--white);overflow:hidden}
.course-date{position:absolute;left:16px;top:11px;font-size:7.3px;color:#444;padding-bottom:4px;border-bottom:1px solid var(--line);white-space:nowrap}
.course-date i{font-style:normal;margin:0 5px}
.course-name{position:absolute;left:16px;top:35px;width:140px;font-size:9.6px;line-height:12px;color:var(--ink)}
.course-name b{color:var(--brand-red);font-weight:400;font-size:7px}
.course-tags{position:absolute;left:15px;top:69px;display:flex;height:17px}
.tag-duration{border:1px solid #cfcfcf;border-right:none;background:#f7f7f7;font-size:7px;color:#333;padding:0 5px 0 6px;display:flex;align-items:center}
.tag-location{background:var(--tag-dark);color:var(--white);font-size:8.5px;font-weight:600;padding:0 12px 0 8px;display:flex;align-items:center;clip-path:polygon(7px 0,100% 0,calc(100% - 5px) 100%,0 100%);margin-left:-4px;padding-left:12px;letter-spacing:.3px}
.course-price{position:absolute;left:16px;top:96px;font-size:14.5px;font-weight:700;color:var(--green)}
.course-discount{position:absolute;right:-1px;bottom:-1px;width:57px;height:35px;background:linear-gradient(180deg,#f5f5f5,#fff);border-left:1px solid #cfcfcf;border-top:1px solid #e2e2e2;padding:9px 0 0 8px}
.discount-label{font-size:6.3px;color:#444;letter-spacing:.2px}
.discount-value{font-size:10px;color:var(--ink)}

/* banner */
.banner{left:0;top:831px;width:716px;height:241px;background:linear-gradient(100deg,#7a7468 0%,#c7a428 32%,#9d9a90 55%,#d7d6d1 70%,#e2e0dc 100%)}
.banner-frame{left:455px;top:871px;width:145px;height:164px;border:12px solid rgba(255,255,255,.85)}
.banner-headline{left:388px;top:922px;font-size:24px;font-weight:700;line-height:26px;color:#2a2a2a;letter-spacing:.2px}
.banner-tag{left:387px;top:980px;width:196px;height:14px;background:var(--green);color:#2a2a2a;font-size:6px;display:flex;align-items:center;justify-content:center}

/* footer */
.footer{left:0;top:1072px;width:716px;height:108px;background:var(--dark)}
.footer .brand{left:135px;top:35px}
.follow{position:absolute;left:160px;top:63px;display:flex;align-items:center;gap:4px;font-size:6.5px;color:#ddd}
.follow .icons{display:flex;gap:2px;margin-left:2px}
.follow .icons span{width:10px;height:10px;background:#111;border-radius:1px;display:block}
.footer .nav{left:369px;top:41px;color:#ddd}
.contact{position:absolute;top:63px;display:flex;align-items:center;gap:8px;font-size:6.2px;color:#ddd}
.contact-icon{width:14px;height:14px;background:#111;display:flex;align-items:center;justify-content:center}
.to-top{left:601px;top:1165px;width:21px;height:22px;background:var(--white);border:1px solid #ccc;display:flex;align-items:center;justify-content:center}
.bottombar{left:0;top:1180px;width:716px;height:20px;background:var(--green);font-size:5.5px;color:#2a2a2a;display:flex;align-items:center;justify-content:center}
</style>
</head>
<body>
<div class="page">

  <div class="abs topbar">
    <div class="social"><span></span><span></span><span></span><span></span></div>
    <div class="student-btn">Student Access</div>
    <div class="search"><svg width="6" height="6" viewBox="0 0 10 10"><circle cx="4" cy="4" r="3" fill="none" stroke="#222" stroke-width="1.6"/><line x1="6.3" y1="6.3" x2="9" y2="9" stroke="#222" stroke-width="1.6"/></svg></div>
  </div>

  <header class="abs header">
    <div class="brand">
      <span class="brand-mark"></span>
      <div><div class="brand-name">RIDGELINE SAFETY</div><div class="brand-sub">SAFETY AND TRAINING</div></div>
    </div>
    <nav class="nav"><span class="active">Home</span><span>Courses</span><span>Our Services</span><span>About us</span><span>Funding</span><span>Locations</span><span>Contact us</span></nav>
  </header>

  <section class="abs difference">
    <h1 class="section-title">THE RIDGELINE SAFETY DIFFERENCE</h1>
    <p class="section-title">Committed to helping our students succeed.</p>
    <div class="rule"></div>

    <div class="tile" style="left:135px;top:86px"><div class="tile-img img-dirt" role="img" aria-label="Loader working in a quarry, aerial view"></div><div class="tile-label">All Courses</div></div>
    <div class="tile" style="left:224px;top:86px"><div class="tile-img img-sky" role="img" aria-label="Gloved handshake against blue sky"></div><div class="tile-label">Funded courses</div></div>
    <div class="tile" style="left:316px;top:86px"><div class="tile-img img-quarry" role="img" aria-label="Red tipper truck at a quarry"></div><div class="tile-label">Mining</div></div>
    <div class="tile" style="left:408px;top:86px"><div class="tile-img img-site" role="img" aria-label="Excavator on a construction site"></div><div class="tile-label">Standard 11</div></div>
    <div class="tile" style="left:500px;top:86px"><div class="tile-img img-roof" role="img" aria-label="Workers with harnesses working at heights"></div><div class="tile-label">Work safely at heights</div></div>

    <div class="tile" style="left:135px;top:195px"><div class="tile-img img-office" role="img" aria-label="Business meeting at a laptop"></div><div class="tile-label">Corporate clients</div></div>
    <div class="tile" style="left:224px;top:195px"><div class="tile-img img-team" role="img" aria-label="Group studying at a laptop"></div><div class="tile-label">Online courses</div></div>
    <div class="tile" style="left:316px;top:195px"><div class="tile-img img-hardhat" role="img" aria-label="Site workers in hard hats reviewing plans"></div><div class="tile-label">RPL's &amp; VOC's</div></div>
    <div class="tile" style="left:408px;top:195px"><div class="tile-img img-lift" role="img" aria-label="Operator beside a yellow elevated work platform"></div><div class="tile-label">Plant &amp; Equipment</div></div>
    <div class="tile" style="left:500px;top:195px"><div class="tile-img img-build" role="img" aria-label="Construction worker in hi-vis on a building frame"></div><div class="tile-label">Construction</div></div>
  </section>

  <h2 class="section-title timetable-title">TIME TABLE</h2>
  <div class="abs timetable-rule"></div>

  <div class="filter active" style="left:163px">
    <div class="filter-label">LOCATION<b>*</b></div><div class="filter-value">YATALA</div>
    <svg width="7" height="5" viewBox="0 0 10 6"><path d="M1 1l4 4 4-4" fill="none" stroke="#333" stroke-width="1.6"/></svg>
  </div>
  <div class="filter" style="left:299px">
    <div class="filter-label">COURSE<b>*</b></div><div class="filter-value">SELECT COURSE</div>
    <svg width="7" height="5" viewBox="0 0 10 6"><path d="M1 1l4 4 4-4" fill="none" stroke="#333" stroke-width="1.6"/></svg>
  </div>
  <div class="filter" style="left:435px">
    <div class="filter-label">MONTH<b>*</b></div><div class="filter-value">SELECT MONTH</div>
    <svg width="7" height="5" viewBox="0 0 10 6"><path d="M1 1l4 4 4-4" fill="none" stroke="#333" stroke-width="1.6"/></svg>
  </div>

  <article class="course-card" style="left:99px;top:526px">
    <div class="course-date">29 October 2019<i>|</i>8:00 AM</div>
    <div class="course-name">RIIHAN304D Work safely at heights <b>*</b></div>
    <div class="course-tags"><span class="tag-duration">1 DAY</span><span class="tag-location">YATALA</span></div>
    <div class="course-price">$500.00</div>
    <div class="course-discount"><div class="discount-label">DISCOUNT</div><div class="discount-value">$120.00</div></div>
  </article>
  <article class="course-card" style="left:276px;top:526px">
    <div class="course-date">29 October 2019<i>|</i>8:00 AM</div>
    <div class="course-name">RIIHAN304D Work safely at heights</div>
    <div class="course-tags"><span class="tag-duration">1 DAY</span><span class="tag-location">YATALA</span></div>
    <div class="course-price">$500.00</div>
    <div class="course-discount"><div class="discount-label">DISCOUNT</div><div class="discount-value">$120.00</div></div>
  </article>
  <article class="course-card" style="left:454px;top:526px">
    <div class="course-date">30 January 2020<i>|</i>8:00 AM</div>
    <div class="course-name">HLTAID005 Confined space - practical</div>
    <div class="course-tags"><span class="tag-duration">1/2 DAY</span><span class="tag-location">YATALA</span></div>
    <div class="course-price">$80.00</div>
  </article>
  <article class="course-card" style="left:99px;top:667px">
    <div class="course-date">15 November 2020<i>|</i>8:00 AM</div>
    <div class="course-name">HLTAID001 First Aid - practical only</div>
    <div class="course-tags"><span class="tag-duration">1/2 DAY</span><span class="tag-location">YATALA</span></div>
    <div class="course-price">$80.00</div>
  </article>
  <article class="course-card" style="left:277px;top:667px">
    <div class="course-date">28 October 2019<i>|</i>8:00 AM</div>
    <div class="course-name">CPCCCM208 Dogging &amp; TLILIC0005</div>
    <div class="course-tags"><span class="tag-duration">1 DAY</span><span class="tag-location">YATALA</span></div>
    <div class="course-price">$500.00</div>
    <div class="course-discount"><div class="discount-label">DISCOUNT</div><div class="discount-value">$1200.00</div></div>
  </article>

  <section class="abs banner" role="img" aria-label="Large yellow mining haul truck on a dusty mine site"></section>
  <div class="abs banner-frame"></div>
  <div class="abs banner-headline">Training a Safety<br>Culture that Counts</div>
  <div class="abs banner-tag">NOW TRAINING - Working at Heights &amp; Confined Spaces courses</div>

  <footer class="abs footer">
    <div class="brand"><span class="brand-mark"></span><div class="brand-name">RIDGELINE SAFETY</div></div>
    <div class="follow">Follow us on :-<div class="icons"><span></span><span></span><span></span><span></span></div></div>
    <nav class="nav"><span>Home</span><span>Courses</span><span>Our Services</span><span>About us</span><span>Funding</span><span>Locations</span><span>Contact us</span></nav>
    <div class="contact" style="left:351px">
      <span class="contact-icon"><svg width="6" height="8" viewBox="0 0 10 14"><path d="M5 0a5 5 0 0 0-5 5c0 4 5 9 5 9s5-5 5-9a5 5 0 0 0-5-5z" fill="#fff"/><circle cx="5" cy="5" r="2" fill="#111"/></svg></span>
      14 Quarry Road, Yatala QLD 4207
    </div>
    <div class="contact" style="left:493px">
      <span class="contact-icon"><svg width="8" height="6" viewBox="0 0 12 9"><rect width="12" height="9" fill="#fff"/><path d="M0 0l6 5 6-5" fill="none" stroke="#111" stroke-width="1.2"/></svg></span>
      info@ridgelinesafety.edu.au
    </div>
  </footer>

  <div class="abs to-top"><svg width="8" height="5" viewBox="0 0 10 6"><path d="M1 5l4-4 4 4" fill="none" stroke="#333" stroke-width="1.6"/></svg></div>
  <div class="abs bottombar">© Copyright All Right Reserved | Powered by Ridgeline Safety.</div>

</div>
</body>
</html>
```